Garden Design Flier

I would like a PDF of this half page A4 flier in soft green tones with dark green leaves.

Target Market(s)

Home owners and real estate agents

Font styles to use
Serif
Other font styles liked:
• Papyrus

Colors
acd136
9bcb3c
cadf82
fefdec

Requirements
Must have
• Green tones
Nice to have
• Leaves, vines, lawns
Should not have
• Open to ideas, but classic style

```html
<!DOCTYPE html>
<html lang="en">
<head>
<meta charset="utf-8">
<title>Bramble Gardens – Flier</title>
<link rel="stylesheet" href="https://fonts.googleapis.com/css2?family=Playfair+Display:ital,wght@0,700;1,400&family=PT+Serif:ital,wght@0,400;0,700;1,400&display=swap">
<style>
  :root {
    --mint: #52e28b;
    --leaf-deep: #04140a;
    --leaf-mid: #0f4a26;
    --leaf-light: #1f7a43;
    --bar: #000;
    --backdrop: #e6e7ea;
  }
  * { box-sizing: border-box; margin: 0; padding: 0; }
  html, body {
    width: 1200px; height: 880px; overflow: hidden;
    background: var(--backdrop);
  }
  .flier {
    position: absolute; left: 20px; top: 30px;
    width: 1160px; height: 820px; overflow: hidden;
    color: var(--mint);
  }
  .flier__foliage {
    position: absolute; inset: 0;
    background:
      radial-gradient(ellipse at 20% 25%, var(--leaf-light) 0%, transparent 45%),
      radial-gradient(ellipse at 80% 70%, var(--leaf-mid) 0%, transparent 50%),
      radial-gradient(ellipse at 60% 20%, var(--leaf-mid) 0%, transparent 40%),
      radial-gradient(ellipse at 30% 85%, var(--leaf-mid) 0%, transparent 45%),
      var(--leaf-deep);
  }
  .flier__content {
    position: absolute; left: 213px; top: 0; width: 727px; height: 100%;
  }
  .business-name {
    position: absolute; left: 0; top: 230px; width: 727px;
    font-family: "PT Serif", serif; font-weight: 700;
    font-size: 76px; line-height: 1; white-space: nowrap;
    display: flex; align-items: center; gap: 22px;
  }
  .business-name__mark {
    width: 30px; height: 30px; background: var(--mint); flex: none;
  }
  .credentials {
    position: absolute; left: 0; top: 386px; width: 727px;
    display: flex; justify-content: space-between;
    font-family: "PT Serif", serif; font-weight: 700;
    font-size: 20px; letter-spacing: 0.06em;
  }
  .services {
    position: absolute; left: -2px; top: 490px; width: 731px;
    display: flex; justify-content: space-between; list-style: none;
    font-family: "Playfair Display", serif; font-weight: 700;
    font-size: 44px; line-height: 1;
  }
  .summary {
    position: absolute; left: 0; top: 560px; width: 727px;
    font-family: "Playfair Display", serif; font-style: italic;
    font-size: 18.5px; line-height: 23px; letter-spacing: 0.04em;
    text-align: center;
  }
  .contact-bar {
    position: absolute; left: 2px; top: 697px; width: 720px; height: 48px;
    background: var(--bar);
    display: flex; align-items: center; justify-content: space-around;
    font-family: "PT Serif", serif; font-size: 15px; letter-spacing: 0.08em;
  }
  .contact-bar__item { display: flex; align-items: center; gap: 10px; }
  .contact-bar__icon { width: 18px; height: 18px; fill: var(--mint); }
</style>
</head>
<body>
  <main class="flier">
    <div class="flier__foliage" role="img" aria-label="Dark green leaves filling the whole background"></div>
    <div class="flier__content">
      <h1 class="business-name"><span class="business-name__mark"></span>Bramble Gardens</h1>

      <div class="credentials">
        <span class="credentials__owner">by Aidan Marlow</span>
        <span class="credentials__qualification">Certificate 3. Horticulture. Regional Institute</span>
      </div>

      <ul class="services">
        <li>Design</li><li>Install</li><li>Grow</li><li>Tend</li><li>Enjoy</li>
      </ul>

      <p class="summary">All your gardening and landscaping needs from design and installation to general maintenance Bespoke vegetable gardens and potager designs created to suite your site and requirements</p>

      <div class="contact-bar">
        <span class="contact-bar__item">
          <svg class="contact-bar__icon" viewBox="0 0 24 24" aria-hidden="true"><path d="M2 5h20v14H2z M2 5l10 8 10-8" fill="none" stroke="var(--mint)" stroke-width="2"/></svg>
          aidan@bramblegardens.com.au
        </span>
        <span class="contact-bar__item">
          <svg class="contact-bar__icon" viewBox="0 0 24 24" aria-hidden="true"><rect x="6" y="2" width="12" height="20" rx="2" fill="none" stroke="var(--mint)" stroke-width="2"/><circle cx="12" cy="18" r="1.3"/></svg>
          0400-182735
        </span>
        <span class="contact-bar__item">
          <svg class="contact-bar__icon" viewBox="0 0 24 24" aria-hidden="true"><rect x="3" y="3" width="14" height="18" rx="1.5"/><circle cx="17" cy="17" r="6" fill="var(--bar)"/><circle cx="17" cy="17" r="5"/><path d="M14.5 17l1.8 1.8 3.2-3.4" fill="none" stroke="var(--bar)" stroke-width="1.6"/></svg>
          12905716384
        </span>
      </div>
    </div>
  </main>
</body>
</html>
```